I need new business cards designed

I would like to get some new designs on business cards. I will upload my logo for reference. The business cards that were designed for me a few months ago were too difficult for the print companies to work with. My company is Quillbrook.net LLC. It is an art company that sells painting and expression cards online.

```html
<!DOCTYPE html>
<html lang="en">
<head>
<meta charset="utf-8">
<title>Quillbrook.net LLC – Business Cards</title>
<link href="https://fonts.googleapis.com/css2?family=Open+Sans:wght@400;600;700&display=swap" rel="stylesheet">
<style>
  :root {
    --backdrop: #2a2a2a;
    --card: #151515;
    --brand-blue: #00a3dd;
    --brand-red: #e8352b;
    --brand-indigo: #3b3d8f;
    --brand-orange: #f7941d;
    --ink-light: #f2f2f2;
  }
  * { margin: 0; padding: 0; box-sizing: border-box; }
  html, body {
    width: 1200px; height: 900px; overflow: hidden;
    background: var(--backdrop);
    font-family: "Open Sans", Arial, sans-serif;
  }
  .stage {
    width: 1200px; height: 900px;
    display: flex; align-items: center; justify-content: center; gap: 50px;
  }
  .card {
    position: relative;
    width: 525px; height: 300px;
    background: var(--card);
    border-radius: 22px;
    overflow: hidden;
  }
  .card-back { border-bottom: 6px solid var(--brand-blue); }

  /* front */
  .wave { position: absolute; inset: 0; width: 100%; height: 100%; }
  .social-row { position: absolute; left: 22px; top: 28px; display: flex; gap: 6px; }
  .social-row span { width: 22px; height: 22px; background: var(--brand-blue); display: block; }

  .brand { position: absolute; display: flex; align-items: center; gap: 10px; }
  .brand-mark { background: var(--brand-orange); display: block; flex: none; }
  .brand-name { color: var(--brand-indigo); font-weight: 400; white-space: nowrap; }
  .front-brand { left: 36px; top: 130px; }
  .front-brand .brand-mark { width: 40px; height: 40px; }
  .front-brand .brand-name { font-size: 24px; }

  .divider {
    position: absolute; left: 262px; top: 56px;
    width: 1.5px; height: 176px; background: var(--brand-blue);
  }
  .contact { position: absolute; left: 278px; top: 54px; color: var(--ink-light); }
  .person-name {
    color: var(--brand-blue); font-weight: 700; font-size: 20px;
    letter-spacing: .5px; text-transform: uppercase; line-height: 1.1;
  }
  .person-role { font-size: 12px; margin-bottom: 8px; }
  .address { font-size: 12px; line-height: 1.45; margin-bottom: 8px; }
  .contact-list { list-style: none; font-size: 12px; line-height: 1.6; }
  .contact-list li { display: flex; align-items: center; gap: 7px; }
  .contact-list svg { width: 12px; height: 12px; flex: none; }

  /* back */
  .back-brand { left: 50%; top: 50%; transform: translate(-50%, -50%); gap: 16px; }
  .back-brand .brand-mark { width: 70px; height: 70px; }
  .back-brand .brand-name { font-size: 40px; }
</style>
</head>
<body>
<main class="stage">
  <section class="card card-front">
    <svg class="wave" viewBox="0 0 525 300" preserveAspectRatio="none" aria-hidden="true">
      <path d="M0,262 C160,262 330,246 525,270 L525,277 C330,253 160,269 0,269 Z" fill="var(--brand-red)"/>
      <path d="M0,274 C160,274 330,258 525,281 L525,300 L0,300 Z" fill="var(--brand-blue)"/>
    </svg>

    <div class="social-row" aria-label="Social media">
      <span></span><span></span><span></span>
    </div>

    <div class="brand front-brand">
      <span class="brand-mark"></span>
      <span class="brand-name">Quillbrook.net</span>
    </div>

    <div class="divider"></div>

    <div class="contact">
      <h1 class="person-name">Nora Pellam</h1>
      <p class="person-role">Managing Director</p>
      <p class="address">Your address, City<br>State, Zip 1234</p>
      <ul class="contact-list">
        <li>
          <svg viewBox="0 0 12 12"><path fill="var(--brand-blue)" d="M2.5 1 L4.5 1 L5.3 3.4 L4 4.3 C4.6 5.8 6 7.2 7.6 7.9 L8.5 6.6 L11 7.4 L11 9.5 C11 10.3 10.3 11 9.5 11 C5 11 1 7 1 2.5 C1 1.7 1.7 1 2.5 1 Z"/></svg>
          123-456-7890
        </li>
        <li>
          <svg viewBox="0 0 12 12"><path d="M1 2.5 H11 V9.5 H1 Z M1.6 3 L6 6.3 L10.4 3" fill="none" stroke="var(--brand-blue)" stroke-width="1.2"/></svg>
          info@quillbrook.net
        </li>
        <li>
          <svg viewBox="0 0 12 12"><circle cx="6" cy="6" r="4.8" fill="none" stroke="var(--brand-blue)" stroke-width="1.3"/><path d="M1.2 6 H10.8 M6 1.2 C3.8 4 3.8 8 6 10.8 M6 1.2 C8.2 4 8.2 8 6 10.8" fill="none" stroke="var(--brand-blue)" stroke-width="1"/></svg>
          www.Quillbrook.net
        </li>
      </ul>
    </div>
  </section>

  <section class="card card-back">
    <div class="brand back-brand">
      <span class="brand-mark"></span>
      <span class="brand-name">Quillbrook.net</span>
    </div>
  </section>
</main>
</body>
</html>
```